Business Cards Design for the electrical wholesaler: clean bold dynamic :)

We need a business card design that would follow our latest brand guidelines. As an electrical wholesaler we want to bring a fresh look and feel into the industry. The design should be clean bold and dynamic. It should come alive with the renewed energy of our green colour. Our grey colour should keep things balanced and complement the notion of maturity and responsibility. We employ Lato as a corporate font however are not bound by this font and we’re open to interpretation here.

Target Market(s)

Electrical contractors

Industry/Entity Type

Business

Contact Information for Business Card

Logo
Name & Surname: Halyna Dorosh
Job Title: Director of Marketing
Email: halya.dorosh@quillmail.example
Cell phone: XXX.XXX.XXXX
Address: 20517 - 87 Ave. Edmonton, AB, Canada. T6K 4N8
Business Phone: 780.555.0184
Website: www.brovix.example

Font styles to use
Other font styles liked:
• Lato

Requirements
Must have
• Logo & website
Nice to have
• Brand elements - some of them you may find in the attached Brand Guidelines (e.g. three lines on the background signifying "W")

```html
<!DOCTYPE html>
<html lang="en">
<head>
<meta charset="utf-8">
<title>Brovix business cards</title>
<link href="https://fonts.googleapis.com/css2?family=Exo+2:wght@500;600&family=Roboto:wght@400&display=swap" rel="stylesheet">
<style>
  :root {
    --backdrop: #b9b9b9;
    --charcoal: #404347;
    --charcoal-light: #4a4d51;
    --paper: #f3f3f2;
    --green: #72b425;
    --green-dark: #62a01c;
    --ink: #3c3e40;
    --icon: #74b32a;
  }
  * { margin: 0; padding: 0; box-sizing: border-box; }
  html, body { width: 1200px; height: 576px; overflow: hidden; }
  body {
    background: var(--backdrop);
    position: relative;
    font-family: "Roboto", Arial, sans-serif;
  }
  .card {
    position: absolute;
    border-radius: 11px;
    overflow: hidden;
  }
  .card-back {
    left: 82px; top: 138px; width: 485px; height: 294px;
    background: var(--charcoal);
  }
  .card-front {
    left: 602px; top: 138px; width: 481px; height: 292px;
    background: var(--paper);
  }
  .card svg.backdrop { position: absolute; inset: 0; }
  .brand {
    position: absolute;
    display: flex;
    align-items: center;
    font-family: "Exo 2", Arial, sans-serif;
    font-weight: 500;
    letter-spacing: 0.5px;
  }
  .brand-mark { border-radius: 50%; background: var(--green); }
  .card-back .brand {
    left: 0; right: 0; top: 124px; justify-content: center; gap: 12px;
    font-size: 44px; color: #ffffff;
  }
  .card-back .brand-mark { width: 34px; height: 34px; }
  .card-front .brand {
    left: 18px; top: 34px; gap: 8px;
    font-size: 30px; color: var(--ink);
  }
  .card-front .brand-mark { width: 24px; height: 24px; }
  .holder {
    position: absolute; left: 19px; top: 142px;
  }
  .holder-name {
    font-family: "Exo 2", Arial, sans-serif;
    font-weight: 600; font-size: 20px; color: var(--green);
    line-height: 24px;
  }
  .holder-title { font-size: 12.5px; color: var(--ink); line-height: 16px; }
  .address {
    position: absolute; left: 19px; top: 204px;
    font-size: 12.5px; line-height: 17px; color: var(--ink);
  }
  .contacts {
    position: absolute; left: 19px; top: 247px;
    font-size: 12.5px; color: var(--ink);
  }
  .contact-row { display: flex; align-items: center; gap: 6px; height: 18px; }
  .contact-item { display: flex; align-items: center; gap: 6px; margin-right: 4px; }
  .icon { width: 12px; height: 12px; flex: none; }
</style>
</head>
<body>

<section class="card card-back" aria-label="Card back">
  <svg class="backdrop" width="485" height="294" viewBox="0 0 485 294" aria-hidden="true">
    <polygon points="185,30 485,30 485,294 300,294" fill="var(--charcoal-light)" opacity="0.55"/>
  </svg>
  <div class="brand"><span class="brand-mark"></span>brovix</div>
</section>

<section class="card card-front" aria-label="Card front">
  <svg class="backdrop" width="481" height="292" viewBox="0 0 481 292" aria-hidden="true">
    <polygon points="206,0 481,0 481,292 370,292" fill="var(--green)"/>
    <polygon points="420,0 481,0 481,292 460,292" fill="var(--green-dark)"/>
  </svg>

  <div class="brand"><span class="brand-mark"></span>brovix</div>

  <div class="holder">
    <p class="holder-name">Oren Castell</p>
    <p class="holder-title">Founder &amp; CEO</p>
  </div>

  <p class="address">20517 - 87 Ave. Edmonton,<br>AB, Canada T6K 4N8</p>

  <div class="contacts">
    <div class="contact-row">
      <svg class="icon" viewBox="0 0 12 12" aria-hidden="true"><circle cx="6" cy="6" r="6" fill="var(--icon)"/><path d="M3.6 3.4c.3-.3.7-.3.9 0l.7.9c.2.3.1.6-.1.8l-.3.3c.3.7.9 1.3 1.6 1.6l.3-.3c.2-.2.5-.3.8-.1l.9.7c.3.2.3.6 0 .9l-.4.4c-.5.5-2 .1-3.3-1.2S2.7 4.3 3.2 3.8z" fill="#fff"/></svg>
      <span>+1 780-555-0184</span>
    </div>
    <div class="contact-row">
      <span class="contact-item">
        <svg class="icon" viewBox="0 0 12 12" aria-hidden="true"><circle cx="6" cy="6" r="6" fill="var(--icon)"/><rect x="3" y="4" width="6" height="4.2" fill="#fff"/><path d="M3 4l3 2.3L9 4" stroke="var(--icon)" stroke-width="0.7" fill="none"/></svg>
        <span>hello@brovix.example</span>
      </span>
      <span class="contact-item">
        <svg class="icon" viewBox="0 0 12 12" aria-hidden="true"><circle cx="6" cy="6" r="6" fill="var(--icon)"/><circle cx="6" cy="6" r="3" fill="none" stroke="#fff" stroke-width="0.8"/><path d="M3 6h6M6 3c-1.2 1.6-1.2 4.4 0 6M6 3c1.2 1.6 1.2 4.4 0 6" fill="none" stroke="#fff" stroke-width="0.6"/></svg>
        <span>www.brovix.example</span>
      </span>
    </div>
  </div>
</section>

</body>
</html>
```